Redesign 2016 Digital Marketing Website and Convert to Wordpress

Technology needed to integrate:

- redesign and convert to wordpress
- gravity forms
- malware and hacker defense / honeypot (must be very secure from hackers)
- I want gravity forms to be a flow that asks many questions with icons and progress bar.
- 1 home page design
- 1 blog design
- 1 design for internal page content
- 1 multi step gravity form
I want to focus on SMB's. We are a marketing agency thats been around since 2016.

Site is: tallpine.agency

I am looking to redesign the homepage, blog page and services page. The services page will be a template for all inner pages of the site. All content needs to be moved into the new design.

I want to get ride of the weird video.

I need you to install gravity forms pro model so we can pass utms.

I need the gravity form to be a multi step form with icons.

All "contact us" or "get a free assesments" call to actions will go to this form only.

step 1:
what is your website

step 2:
what industry are you in
- option
- Home Services
- Legal
- Ecommerce
- Lead Gen

No matter which one they select its going to produce a differnt calculator for them.

Law:
How many leads did you get last month
how much is each ase worth on average
How much revenue do you want to make

Home servicse:
How many bookings did you get last month
How much is each service worht on average
How much revenue do you wangt to make

Ecommerce:
What is your average order value
How muny purchases did you have last month
How much revenue did you drive
How much revenue do you want to drive

For lead gen:
How many leads did you get lawt month
How much revenue did they generate

Step 3:
What is your current advertising budget

step 4:
Do you have a CRM and if so what is it

Step 5:
What is your personal informagtion
name
email
phone

Let me know if this is enough to get you going

Small and medium sized law firms, ecommerce, home services and lead gen customers.

We are a digital marketing agency

• Use whats on the current site and improve upon it

• Must be very secure, developed into a wordpress website. using gravity forms. remove my photo and my staffs photo, depersonalize it so it doesnt mention me or sam crolley. Use the same color scheme. I am looking to redesign the homepage, blog page and services page. The services page will be a template for all inner pages of the site. All content needs to be moved into the new design. I want to get ride of the weird video. I need you to install gravity forms pro model so we can pass utms. I need the gravity form to be a multi step form with icons. All "contact us" or "get a free assesments" call to actions will go to this form only. step 1: what is your website step 2: what industry are you in - option - Home Services - Legal - Ecommerce - Lead Gen No matter which one they select its going to produce a differnt calculator for them. Law: How many leads did you get last month how much is each ase worth on average How much revenue do you want to make Home servicse: How many bookings did you get last month How much is each service worht on average How much revenue do you wangt to make Ecommerce: What is your average order value How muny purchases did you have last month How much revenue did you drive How much revenue do you want to drive For lead gen: How many leads did you get lawt month How much revenue did they generate How much revenue do you want to make Step 3: What is your current advertising budget step 4: Do you have a CRM and if so what is it Step 5: What is your personal informagtion name email phone Let me know if this is enough to get you going
• SHOULD NOT BE SLOPPY, I AM LOOKING FOR ATTENTION TO DETAIL.

```html
<!DOCTYPE html>
<html lang="en">
<head>
<meta charset="utf-8">
<title>Tall Pine Growth Marketing – Grow Your Revenue</title>
<link href="https://fonts.googleapis.com/css2?family=Poppins:wght@300;400;500;600;700;800&display=swap" rel="stylesheet">
<style>
  :root{
    --maroon:#751618;
    --orange:#f7941d;
    --ink:#333333;
    --nav:#2d2d2d;
    --muted:#444444;
    --line:#e2e2e2;
    --step-off:#c4c4c4;
    --white:#ffffff;
  }
  *{box-sizing:border-box;margin:0;padding:0}
  html,body{width:1115px;height:1200px;overflow:hidden;background:var(--white)}
  body{position:relative;font-family:"Poppins",sans-serif;color:var(--ink)}
  a{color:inherit;text-decoration:none}

  /* header */
  .site-header{position:absolute;top:0;left:0;width:1115px;height:84px}
  .brand{position:absolute;display:flex;align-items:center;gap:12px}
  .brand-mark{width:57px;height:57px;border-radius:50%;background:var(--maroon);flex:none}
  .brand-name{font-weight:300;font-size:23px;letter-spacing:2px;color:#666;line-height:1}
  .brand-tag{font-weight:400;font-size:8.5px;letter-spacing:4px;color:#555;margin-top:8px;line-height:1}
  .site-header .brand{left:70px;top:13px}
  .call{position:absolute;left:525px;top:30px;font-weight:600;font-size:16.5px;color:#444}
  .call strong{color:var(--maroon);font-weight:700}
  .cta{position:absolute;left:838px;top:19px;width:209px;height:45px;background:var(--orange);color:var(--white);
       font-weight:600;font-size:14px;display:flex;align-items:center;justify-content:center;letter-spacing:.3px}

  .main-nav{position:absolute;top:84px;left:0;width:1115px;height:51px;background:var(--nav);
            display:flex;justify-content:center;align-items:center;gap:43px}
  .main-nav a{color:var(--white);font-size:13.5px;letter-spacing:.4px}

  /* form */
  .form-title{position:absolute;top:183px;left:0;width:1115px;text-align:center;font-weight:800;font-size:33px;letter-spacing:.5px;color:var(--ink)}
  .form-title-rule{position:absolute;top:238px;left:514px;width:87px;height:3px;background:var(--maroon)}

  .progress{position:absolute;top:282px;left:252px;width:612px;height:54px}
  .progress-track{position:absolute;top:26px;left:27px;width:558px;height:2px;background:var(--step-off)}
  .progress-fill{position:absolute;top:26px;left:27px;width:230px;height:2px;background:var(--maroon)}
  .progress-step{position:absolute;top:0;width:54px;height:54px;border-radius:50%;background:var(--white);
                 border:2px solid var(--step-off);color:var(--step-off);font-weight:700;font-size:21px;
                 display:flex;align-items:center;justify-content:center}
  .progress-step.is-done{background:var(--maroon);border-color:var(--maroon);color:var(--white)}

  .step-head{position:absolute;top:385px;left:70px;display:flex;gap:12px}
  .step-head svg{margin-top:2px}
  .step-label{font-weight:700;font-size:17px;color:var(--maroon);line-height:1.2}
  .step-question{font-size:15.5px;color:var(--ink);margin-top:6px}
  .btn-next{position:absolute;top:385px;left:940px;width:107px;height:47px;background:var(--nav);color:var(--white);
            font-weight:700;font-size:18px;display:flex;align-items:center;justify-content:center;gap:12px;letter-spacing:.5px}

  .industry-options{position:absolute;top:452px;left:70px;display:flex;gap:9px}
  .industry-option{width:188px;height:52px;border:1px solid #cfcfcf;background:var(--white);display:flex;align-items:center;
                   justify-content:center;gap:12px;font-weight:500;font-size:14px;color:var(--ink)}
  .industry-option svg{fill:#555}
  .industry-option.is-selected{background:#000;border-color:#000;color:var(--white)}
  .industry-option.is-selected svg{fill:var(--white)}

  /* footer */
  .footer-band{position:absolute;top:614px;left:0;width:1115px;height:140px;border-top:1px solid var(--line);border-bottom:1px solid var(--line)}
  .footer-band .brand{left:70px;top:40px}
  .partner-badge{position:absolute;left:386px;top:28px;width:192px;height:82px;display:flex;gap:14px}
  .partner-badge .stripe{width:22px;height:82px;background:#e2483d}
  .partner-badge .panel{flex:1;background:#ececec;border-radius:4px}
  .review-badge{position:absolute;left:638px;top:28px;width:82px;height:82px;border-radius:50%;background:#1d3d5c}
  .follow{position:absolute;left:822px;top:32px}
  .follow h3{font-weight:500;font-size:17px;letter-spacing:.5px;color:var(--ink)}
  .social{display:flex;gap:25px;margin-top:18px}
  .social span{width:28px;height:28px;background:#3a3a3a;border-radius:4px;display:block}

  .footer-cols{position:absolute;top:790px;left:0;width:1115px}
  .footer-col{position:absolute;top:0}
  .footer-col h4{font-weight:700;font-size:21.5px;color:var(--ink);letter-spacing:.3px;margin-bottom:11px}
  .footer-col li{list-style:none;font-size:12.5px;color:var(--muted);letter-spacing:.3px;line-height:20px;margin-bottom:10.5px}
  .col-links{left:70px}
  .col-services{left:296px}
  .col-industries{left:571px}
  .col-guides{left:821px;width:230px}
  .col-guides li{margin-bottom:11px}

  .legal{position:absolute;top:1120px;left:0;width:1115px;height:80px;border-top:1px solid var(--line);
         text-align:center;padding-top:28px;font-size:12.5px;color:var(--muted);letter-spacing:.2px}
</style>
</head>
<body>

<header class="site-header">
  <a class="brand" href="#">
    <span class="brand-mark"></span>
    <span>
      <div class="brand-name">TALL PINE</div>
      <div class="brand-tag">GROWTH MARKETING</div>
    </span>
  </a>
  <div class="call">OR CALL US NOW : <strong>(480) 555-0142</strong></div>
  <a class="cta" href="#">GROW YOUR REVENUE</a>
</header>

<nav class="main-nav">
  <a href="#">HOME</a><a href="#">ABOUT</a><a href="#">INDUSTRIES</a><a href="#">SERVICES</a><a href="#">BLOG</a><a href="#">CONTACT US</a>
</nav>

<main>
  <h1 class="form-title">GROW YOUR REVENUE NOW</h1>
  <div class="form-title-rule"></div>

  <div class="progress">
    <div class="progress-track"></div>
    <div class="progress-fill"></div>
    <div class="progress-step is-done" style="left:0">1</div>
    <div class="progress-step is-done" style="left:139px">2</div>
    <div class="progress-step" style="left:279px">3</div>
    <div class="progress-step" style="left:418px">4</div>
    <div class="progress-step" style="left:558px">5</div>
  </div>

  <div class="step-head">
    <svg width="42" height="42" viewBox="0 0 42 42" fill="none" stroke="#751618" stroke-width="1.4">
      <rect x="9" y="2" width="16" height="38"/><rect x="25" y="16" width="13" height="24"/>
      <line x1="2" y1="40" x2="40" y2="40"/>
      <rect x="12" y="6" width="4" height="4"/><rect x="18" y="6" width="4" height="4"/>
      <rect x="12" y="13" width="4" height="4"/><rect x="18" y="13" width="4" height="4"/>
      <rect x="12" y="20" width="4" height="4"/><rect x="18" y="20" width="4" height="4"/>
      <rect x="12" y="27" width="4" height="4"/><rect x="18" y="27" width="4" height="4"/>
      <rect x="28" y="20" width="3" height="3"/><rect x="33" y="20" width="3" height="3"/>
      <rect x="28" y="26" width="3" height="3"/><rect x="33" y="26" width="3" height="3"/>
      <rect x="28" y="32" width="3" height="3"/><rect x="33" y="32" width="3" height="3"/>
    </svg>
    <div>
      <div class="step-label">Step 2</div>
      <div class="step-question">What industry are you in</div>
    </div>
  </div>
  <a class="btn-next" href="#">NEXT
    <svg width="9" height="14" viewBox="0 0 9 14" fill="none" stroke="#fff" stroke-width="1.6"><path d="M1 1l6 6-6 6"/></svg>
  </a>

  <div class="industry-options">
    <div class="industry-option is-selected">
      <svg width="20" height="20" viewBox="0 0 20 20"><rect x="9" y="1" width="9" height="6" rx="1" transform="rotate(45 13.5 4)"/><rect x="1" y="13" width="11" height="3" rx="1.2" transform="rotate(-45 6.5 14.5)"/></svg>
      Law Firm
    </div>
    <div class="industry-option">
      <svg width="22" height="20" viewBox="0 0 22 20"><path d="M11 1L1 10h3v9h5v-6h4v6h5v-9h3z"/></svg>
      Home Services
    </div>
    <div class="industry-option">
      <svg width="26" height="18" viewBox="0 0 26 18"><path d="M6 17a5 5 0 010-10 7 7 0 0113-1 5.5 5.5 0 011 11z"/></svg>
      Saas
    </div>
    <div class="industry-option">
      <svg width="24" height="22" viewBox="0 0 24 22"><path d="M1 2h4l3 11h12l3-8H7"/><circle cx="9" cy="18" r="2"/><circle cx="18" cy="18" r="2"/><path d="M6 5h17l-3 8H8z"/></svg>
      Ecommerce
    </div>
    <div class="industry-option">
      <svg width="30" height="20" viewBox="0 0 30 20"><circle cx="15" cy="6" r="4"/><circle cx="6" cy="8" r="3"/><circle cx="24" cy="8" r="3"/><path d="M8 19a7 6 0 0114 0z"/><path d="M1 19a5 5 0 019-2v2z"/><path d="M29 19a5 5 0 00-9-2v2z"/></svg>
      Lead Gen
    </div>
  </div>
</main>

<footer>
  <div class="footer-band">
    <a class="brand" href="#">
      <span class="brand-mark"></span>
      <span>
        <div class="brand-name">TALL PINE</div>
        <div class="brand-tag">GROWTH MARKETING</div>
      </span>
    </a>
    <div class="partner-badge" role="img" aria-label="Advertising partner badge"><span class="stripe"></span><span class="panel"></span></div>
    <div class="review-badge" role="img" aria-label="Client reviews badge"></div>
    <div class="follow">
      <h3>FOLLOW US</h3>
      <div class="social">
        <span role="img" aria-label="Social profile 1"></span>
        <span role="img" aria-label="Social profile 2"></span>
        <span role="img" aria-label="Social profile 3"></span>
        <span role="img" aria-label="Social profile 4"></span>
        <span role="img" aria-label="Social profile 5"></span>
      </div>
    </div>
  </div>

  <div class="footer-cols">
    <div class="footer-col col-links">
      <h4>QUICK LINKS</h4>
      <ul><li>About</li><li>Industries</li><li>Services</li><li>Resources</li><li>Training</li><li>Blog</li><li>Contact Us</li></ul>
    </div>
    <div class="footer-col col-services">
      <h4>SERVICES</h4>
      <ul><li>Programmatic Advertising</li><li>Search Engine Marketing (SEM)</li><li>Search Engine Optimization (SEO)</li><li>Content Marketing</li><li>Email Marketing</li><li>Paid Search Advertising</li><li>Paid Social Advertising</li></ul>
    </div>
    <div class="footer-col col-industries">
      <h4>INDUSTRIES</h4>
      <ul><li>Ecommerce</li><li>Electricians</li><li>Financial Services Marketing</li><li>Home Builders</li><li>Home Services</li><li>Hvac Companies</li><li>Cosmetic Surgery Centers</li><li>Dental Marketing</li></ul>
    </div>
    <div class="footer-col col-guides">
      <h4>GUIDES</h4>
      <ul><li>Ultimate Guide On Growing Your Medical Practice Business</li><li>Legal Marketing Strategy Guide For Law Firm Offices</li><li>Ultimate Social Ads Guide To Skyrocket Your Leads And Sales</li><li>Ultimate Guide To Search Engine Queries</li></ul>
    </div>
  </div>

  <div class="legal">Copyright © 2024 CompanyName&nbsp; All Rights Reserved. Privacy Policy, Terms Of Use, Press &amp; Media, Cookie Policy</div>
</footer>

</body>
</html>
```